Stationery Set for Velmora Company

I need to create full stationery design for my company; Business Cards, Envelops, Letter Heads, Calendar.
In the letter head and Envelops... only contact information and website links.
Our company is a Service Management company with different domains of innovative services including Technology Service Management, Education Services, Outsourcing Management, Events Management.
I need a modern and innovative design specially for the business card. I some transparent designs and I like it, but don't limit your innovation to what I mentioned. Sky is limit for your innovation.

Target Market(s)

Middle East & Africa

Industry/Entity Type

Business Management

Colors
34a7d8
0355a3
85acd3
86cae7
cee9f5
cfdeed
e4daeb
f3f1f8
ecf7fb

Requirements
Must have
• Name, Title, Email, Mobile
Nice to have
• We have multiple locations in USA, KSA, EGY, so I need ideas about how to include all contact details maybe QR / Barcode or something else.
• Please see our locations and contact information: www.brightvelmora.example
Should not have
• Too much text

```html
<!DOCTYPE html>
<html lang="en">
<head>
<meta charset="utf-8">
<title>Velmora Company – Business Card</title>
<link rel="stylesheet" href="https://fonts.googleapis.com/css2?family=Open+Sans:ital,wght@0,400;0,600;1,400&display=swap">
<style>
  :root {
    --bg: #3c3c3c;
    --card: #ffffff;
    --brand-blue: #3d6ab1;
    --brand-grey: #bdb7b7;
    --ink: #1e1e1e;
    --rule: #3d6ab1;
    --white: #ffffff;
  }
  * { box-sizing: border-box; margin: 0; padding: 0; }
  html, body {
    width: 1105px; height: 1200px; overflow: hidden;
    background: var(--bg);
    font-family: "Open Sans", Arial, sans-serif;
  }
  .canvas { position: relative; width: 1105px; height: 1200px; }

  .card {
    position: absolute; left: 192px; width: 720px; height: 412px;
    overflow: hidden;
  }
  .card--front { top: 140px; background: var(--card); }
  .card--back  { top: 602px; background: var(--brand-blue); }

  .brand-name {
    position: absolute; font-weight: 600; letter-spacing: 0.5px; white-space: nowrap;
  }
  .card--front .brand-name {
    right: 34px; top: 54px; font-size: 34px; color: var(--brand-blue);
    display: flex; align-items: center; gap: 12px;
  }
  .brand-dot {
    width: 14px; height: 14px; border-radius: 50%; background: var(--brand-grey);
  }

  .holder { position: absolute; left: 29px; top: 160px; }
  .holder__name { font-size: 25px; font-weight: 600; color: var(--brand-blue); line-height: 1.1; }
  .holder__title { font-size: 19px; color: var(--ink); margin-top: 4px; }
  .divider {
    position: absolute; left: 29px; top: 220px; width: 647px; height: 1.5px; background: var(--rule);
  }

  .office {
    position: absolute; font-size: 16px; line-height: 22px; color: var(--ink);
    font-style: normal; white-space: nowrap;
  }
  .office__label { font-weight: 600; color: var(--brand-blue); font-size: 17px; }
  .office__phone span { font-weight: 600; color: var(--brand-blue); }
  .office--ksa { left: 29px; top: 227px; }
  .office--usa { left: 279px; top: 249px; }

  .contacts {
    position: absolute; right: 30px; top: 286px; list-style: none;
    font-size: 14px; color: var(--ink); white-space: nowrap;
  }
  .contacts li { display: flex; align-items: center; gap: 9px; height: 27px; }
  .contacts svg { width: 15px; height: 15px; flex: none; }

  .band { position: absolute; left: 0; bottom: 0; width: 720px; height: 19px; }

  .card--back .brand-name {
    left: 0; right: 0; top: 160px; text-align: center; font-size: 54px; color: var(--white);
    display: flex; justify-content: center; align-items: center; gap: 16px;
  }
  .card--back .brand-dot { width: 18px; height: 18px; background: var(--white); }
  .back-url {
    position: absolute; left: 0; right: 0; top: 342px; text-align: center;
    font-size: 18px; font-style: italic; letter-spacing: 2px; color: var(--white);
  }
</style>
</head>
<body>
<main class="canvas">

  <section class="card card--front" aria-label="Business card front">
    <div class="brand-name"><span class="brand-dot"></span>Velmora Company</div>

    <div class="holder">
      <p class="holder__name">Daniel Harlow</p>
      <p class="holder__title">CEO/Founder</p>
    </div>
    <div class="divider"></div>

    <address class="office office--ksa">
      <p class="office__label">SAUDI ARABIA:</p>
      <p>Riyadh, Al Nakheel District,</p>
      <p>Qasr Ridge St.</p>
      <p>Lumen Towers</p>
      <p>Block 4C 3rd Floor C12, C14</p>
      <p class="office__phone"><span>Phone :</span> +966 92000 17 83</p>
    </address>

    <address class="office office--usa">
      <p class="office__label">USA:</p>
      <p>418 Harbor Crest Drive</p>
      <p>5th Floor Maple Bay</p>
      <p>CA 94012 US</p>
      <p class="office__phone"><span>Phone:</span>+1.5550192846</p>
    </address>

    <ul class="contacts">
      <li>
        <svg viewBox="0 0 16 16" aria-hidden="true"><rect x="4" y="1" width="8" height="14" rx="1.5" fill="none" stroke="#3d6ab1" stroke-width="1.6"/><rect x="5.5" y="3" width="5" height="8" fill="#3d6ab1"/></svg>
        +1.5550192846
      </li>
      <li>
        <svg viewBox="0 0 16 16" aria-hidden="true"><rect x="1" y="3.5" width="14" height="9" fill="#3d6ab1"/><path d="M1 3.5 L8 9 L15 3.5" fill="none" stroke="#fff" stroke-width="1.2"/></svg>
        info@brightvelmora.example
      </li>
      <li>
        <svg viewBox="0 0 16 16" aria-hidden="true"><circle cx="8" cy="8" r="7" fill="#3d6ab1"/><path d="M5 5 Q8 4 9 7 Q7 9 5 8 Z M10 10 Q12 9 12 12 Z" fill="#fff"/></svg>
        www.brightvelmora.example
      </li>
    </ul>

    <svg class="band" viewBox="0 0 720 19" preserveAspectRatio="none" aria-hidden="true">
      <polygon points="0,0 528,0 522,19 0,19" fill="var(--brand-blue)"/>
      <polygon points="533,0 720,0 720,19 527,19" fill="var(--brand-grey)"/>
    </svg>
  </section>

  <section class="card card--back" aria-label="Business card back">
    <div class="brand-name"><span class="brand-dot"></span>Velmora Company</div>
    <p class="back-url">www.brightvelmora.example</p>
  </section>

</main>
</body>
</html>
```